Maplecrest Disability - Social Security Disability Attorneys

Our company is expanding to attract clients nationwide for our social security disability practice. We have a logo, but I am looking for a creative and elegant letterhead that projects an image of being technologically advanced but still professional enough for the legal field. I am looking for the "wow factor" combined with this is still professional enough for a law practice.

Requesting letterhead and business card design
Updates

Had to update and change the logo. The previous logo had a typo. Please send updates with the new logo for consideration. The letterhead and business cards should be professional enough to be used for a law firm. Thanks.

Industry/Entity Type

Law Practice, Law Firm, Healthcare Industry, Government

Colors

Designer to choose colors to be used in the design.

Requirements
Nice to have
• **Please create a vertical design for the business card**

```html
<!DOCTYPE html>
<html lang="en">
<head>
<meta charset="utf-8">
<title>Maplecrest Disability – Stationery</title>
<link rel="stylesheet" href="https://fonts.googleapis.com/css2?family=Lato:wght@400;700&family=Roboto:wght@400;500;700&family=Great+Vibes&display=swap">
<style>
  :root {
    --orange: #ef7f2a;
    --blue: #4369d6;
    --brand-blue: #4a63c4;
    --ink: #1e1e1e;
    --paper: #ffffff;
    --backdrop: #bdbdbd;
  }
  * { margin: 0; padding: 0; box-sizing: border-box; }
  html, body { width: 1200px; height: 848px; overflow: hidden; }
  body { background: var(--backdrop); position: relative; font-family: "Lato", sans-serif; color: var(--ink); }

  .brand { display: flex; flex-direction: column; align-items: center; gap: 5px; }
  .brand-dot { width: 9px; height: 9px; border-radius: 50%; background: var(--orange); }
  .brand-name { font-family: "Lato", sans-serif; font-weight: 400; color: var(--brand-blue); letter-spacing: 1.2px; text-transform: uppercase; white-space: nowrap; }

  /* Letterhead */
  .letterhead { position: absolute; left: 151px; top: 118px; width: 455px; height: 624px; background: var(--paper); overflow: hidden; }
  .letterhead .brand { position: absolute; left: 25px; top: 32px; width: 140px; }
  .letterhead .brand-name { font-size: 11px; }
  .lh-contact { position: absolute; left: 321px; top: 38px; border-left: 1px solid var(--orange); padding-left: 6px; font-family: "Roboto", sans-serif; font-size: 7px; line-height: 10.4px; }
  .lh-contact .address { margin-bottom: 2px; }
  .contact-row { display: flex; align-items: center; gap: 5px; }
  .contact-row svg { width: 7px; height: 7px; flex: none; }
  .letter { position: absolute; left: 25px; top: 146px; width: 405px; font-size: 8.4px; line-height: 10.2px; }
  .letter .date { font-size: 9px; margin-bottom: 10px; }
  .letter .block { margin-bottom: 10px; }
  .letter .salutation { font-size: 10.5px; font-weight: 700; margin-bottom: 10px; }
  .letter .body p { text-align: justify; margin-bottom: 9.5px; }
  .letter .regards { margin-top: 16px; }
  .letter .signature { font-family: "Great Vibes", cursive; font-size: 22px; line-height: 30px; margin-top: 8px; }
  .lh-footer { position: absolute; left: 0; bottom: 0; width: 455px; height: 80px; }

  /* Business cards */
  .card { position: absolute; top: 234px; width: 213px; height: 373px; background: var(--paper); overflow: hidden; text-align: center; font-family: "Roboto", sans-serif; }
  .card-front { left: 627px; }
  .card-back { left: 864px; }
  .card .brand { position: absolute; left: 0; width: 100%; }
  .card-front .brand { top: 62px; }
  .card-back .brand { top: 100px; }
  .card .brand-name { font-size: 12.5px; }
  .card-back .brand-name { font-size: 11px; }
  .holder { position: absolute; top: 132px; width: 100%; }
  .holder-name { color: var(--orange); font-weight: 700; font-size: 13px; letter-spacing: 0.2px; }
  .holder-title { display: flex; align-items: center; justify-content: center; gap: 3px; font-size: 10px; margin-top: 2px; }
  .holder-title::before, .holder-title::after { content: ""; width: 27px; height: 1px; background: var(--orange); }
  .card-address { position: absolute; top: 191px; width: 100%; font-size: 9px; line-height: 12.5px; }
  .card-icons { position: absolute; top: 237px; width: 100%; display: flex; justify-content: center; gap: 15px; }
  .card-icons svg { width: 9px; height: 9px; }
  .card-lines { position: absolute; top: 260px; width: 100%; font-size: 9px; line-height: 14px; }
  .card-footer { position: absolute; left: 0; bottom: 0; width: 213px; height: 14px; }
  .industries { position: absolute; top: 278px; width: 100%; color: var(--orange); font-size: 10px; line-height: 13.5px; }
</style>
</head>
<body>

<svg width="0" height="0" style="position:absolute">
  <defs>
    <symbol id="icon-phone" viewBox="0 0 10 10"><path d="M2 0.8 L3.6 2.6 L2.8 3.6 Q4 5.9 6.3 7.2 L7.4 6.4 L9.2 8 L8 9.4 Q3.6 9 0.6 2 Z" fill="#ef7f2a"/></symbol>
    <symbol id="icon-mail" viewBox="0 0 10 10"><rect x="0.5" y="2" width="9" height="6.4" fill="#ef7f2a"/><path d="M0.5 2 L5 5.6 L9.5 2" fill="none" stroke="#fff" stroke-width="0.8"/></symbol>
    <symbol id="icon-globe" viewBox="0 0 10 10"><circle cx="5" cy="5" r="4.5" fill="#ef7f2a"/><path d="M0.5 5 H9.5 M5 0.5 Q2.6 5 5 9.5 M5 0.5 Q7.4 5 5 9.5" fill="none" stroke="#fff" stroke-width="0.6"/></symbol>
  </defs>
</svg>

<section class="letterhead">
  <div class="brand">
    <span class="brand-dot"></span>
    <span class="brand-name">Maplecrest Disability</span>
  </div>

  <div class="lh-contact">
    <div class="address">Suite 4, Level 12, Harbour<br>Lane Sydney NSW 2000</div>
    <div class="contact-row"><svg><use href="#icon-phone"/></svg>555-014-2286</div>
    <div class="contact-row"><svg><use href="#icon-mail"/></svg>info@maplecrestdisability.com</div>
    <div class="contact-row"><svg><use href="#icon-globe"/></svg>www.maplecrestdisability.com</div>
  </div>

  <article class="letter">
    <p class="date">January-03-2020</p>
    <p class="block">Mr, John Doe<br>President</p>
    <p class="block">Birchline Corporation<br>123 Street Name, Suite# 10<br>City, State, 120023</p>
    <p class="salutation">Dear Mr, John</p>
    <div class="body">
      <p>Lorem ipsum dolor sit amet, consectetur adipisicing elit, sed do eiusmod tempor incididunt ut labore et dolore magna aliqua. Ut enim ad minim veniam, quis nostrud exercitation ullamco laboris nisi ut aliquip ex ea commodo consequat. Duis aute irure dolor in reprehenderit in voluptate velit esse cillum dolore eu fugiat nulla pariatur.</p>
      <p>Lorem ipsum dolor sit amet, consectetur adipisicing elit, sed do eiusmod tempor incididunt ut labore et dolore magna aliqua. Ut enim ad minim veniam, quis nostrud exercitation ullamco laboris nisi ut aliquip ex ea commodo consequat. Duis aute irure dolor in reprehenderit in voluptate velit esse cillum dolore eu fugiat nulla pariatur.</p>
      <p>Lorem ipsum dolor sit amet, consectetur adipisicing elit, sed do eiusmod tempor incididunt ut labore et dolore magna aliqua. Ut enim ad minim veniam, quis nostrud exercitation ullamco laboris nisi ut aliquip ex ea commodo consequat.</p>
      <p>Excepteur sint occaecat cupidatat non proident, sunt in culpa qui officia deserunt mollit anim id est laborum. re et dolore magnam aliquam quaerat voluptatem.</p>
    </div>
    <p class="regards">Regards</p>
    <p class="signature">Owen Carter</p>
  </article>

  <svg class="lh-footer" viewBox="0 0 455 80" aria-hidden="true">
    <path d="M0 43 H304 L292 54 Q285 59 276 59 H0 Z" fill="var(--orange)"/>
    <path d="M0 66 H272 Q285 66 295 58 L338 23 Q348 17 362 17 H455 V80 H0 Z" fill="var(--blue)"/>
  </svg>
</section>

<section class="card card-front">
  <div class="brand">
    <span class="brand-dot"></span>
    <span class="brand-name">Maplecrest Disability</span>
  </div>
  <div class="holder">
    <div class="holder-name">DANA WHITFIELD</div>
    <div class="holder-title">Co-Founder</div>
  </div>
  <div class="card-address">Suite 4, Level 12, Harbour<br>Lane Sydney NSW 2000</div>
  <div class="card-icons">
    <svg><use href="#icon-phone"/></svg>
    <svg><use href="#icon-mail"/></svg>
    <svg><use href="#icon-globe"/></svg>
  </div>
  <div class="card-lines">
    555-014-2286<br>info@maplecrestdisability.com<br>www.maplecrestdisability.com
  </div>
  <svg class="card-footer" viewBox="0 0 213 14" aria-hidden="true">
    <path d="M0 1.5 H106 L101 4 H0 Z" fill="var(--orange)"/>
    <path d="M0 7 H88 Q96 7 101 4 L105 2 Q108 0.5 113 0.5 H213 V14 H0 Z" fill="var(--brand-blue)"/>
  </svg>
</section>

<section class="card card-back">
  <div class="brand">
    <span class="brand-dot"></span>
    <span class="brand-name">Maplecrest Disability</span>
  </div>
  <div class="industries">Law Practice, Law Firm,<br>Healthcare Industry, Government</div>
</section>

</body>
</html>
```